The Marlowe - Luxury Health & Wellness Development - Coming Soon - Pre Leasing Flyer

I would like a sophisticated, luxury, high-end flyer designed to have printed/mailed and emailed to select businesses with the opportunity to Pre Lease space in the Luxury Health & Wellness development named "The Marlowe" located in Bluffton, SC. I have already created the logo design for The Marlowe that I would like predominantly displayed on the flyer. I also have an exterior rendering of the building that I would like predominantly displayed. I have uploaded a flyer that I created with a brief description and highlights of the development that you can incorporate in to the flyer design. Lastly, I've uploaded 2 photos of the surrounding landscape that I would like to use in the flyer. I would like the flyer to be more minimalistic in design rather that cluttered and too busy. I would also like parts of the flyer to be in black/white/grayscale with other areas that have pops of color to keep it modern and interesting.
Target Market(s)
Owners of Health & Wellness Businesses. (Medspa's, Plastic Surgeons, Cosmetic Dermatology, Regenerative and Integrative Medicine, Dental Specialty, other speciality medicine)
Industry/Entity Type
Luxury Health & Wellness

```html
<!DOCTYPE html>
<html lang="en">
<head>
<meta charset="utf-8">
<title>The Marlowe – Pre-Leasing Flyer</title>
<link rel="stylesheet" href="https://fonts.googleapis.com/css2?family=Playfair+Display:wght@400;700&family=Jost:wght@400;500;600&display=swap">
<style>
:root{
  --red:#d0303a;
  --ink:#141414;
  --text:#3a3a3a;
  --muted:#555;
  --row:#e9e9e9;
  --line:#dcdcdc;
  --stage:#a9a9a9;
  --paper:#ffffff;
  --dark:#2e2e2e;
}
*{margin:0;padding:0;box-sizing:border-box}
html,body{width:1200px;height:803px;overflow:hidden;background:var(--stage)}
body{font-family:"Jost",Arial,sans-serif;color:var(--text)}
.page{position:absolute;top:79px;width:461px;height:652px;background:var(--paper);overflow:hidden}
.page--front{left:95px}
.page--back{left:625px}
.abs{position:absolute}
.art{position:absolute;left:0;top:0}

/* front */
.brand{left:33px;top:26px;white-space:nowrap;font-family:"Jost",Arial,sans-serif;font-weight:500;font-size:30px;line-height:1;color:var(--ink)}
.panel-text{left:48px;top:356px;width:180px;color:#fff}
.panel-title{font-family:"Playfair Display",Georgia,serif;font-size:23px;line-height:27px;font-weight:400}
.rule{height:1px;background:rgba(255,255,255,.85);width:178px}
.address{font-size:11px;line-height:13.5px;font-weight:500;padding:5px 2px}
.subhead{font-family:"Playfair Display",Georgia,serif;font-weight:400;font-size:15px;margin:10px 0 6px}
.highlights{list-style:none}
.highlights li{position:relative;padding-left:13px;font-size:7.2px;line-height:9px;margin-bottom:6px;font-weight:400}
.highlights li svg{position:absolute;left:0;top:1px}
.section-title{font-family:"Playfair Display",Georgia,serif;font-weight:400;color:var(--red);font-size:15.5px;line-height:1;white-space:nowrap}
.info-box{border:1px solid var(--line);border-radius:3px;background:#fff}
.info-row{position:relative;padding:4px 0 4px 17px;height:29px}
.info-row:nth-child(even){background:var(--row)}
.info-row svg{position:absolute;left:-6px;top:8px}
.info-row b{display:block;font-size:7.4px;font-weight:600;color:#333;line-height:9px}
.info-row span{display:block;font-size:6.6px;color:var(--muted);line-height:10px}
.contact{left:266px;top:611px;width:180px;height:23px}
.contact__name{position:absolute;left:0;top:0;width:88px;height:23px;background:var(--dark);border-radius:6px 0 0 6px;color:#fff;font-family:"Playfair Display",Georgia,serif;font-size:10.5px;line-height:23px;text-align:center}
.contact__lines{position:absolute;left:92px;top:3px;font-size:4.8px;line-height:6.5px;font-weight:600;color:var(--ink);white-space:nowrap}
.contact__base{position:absolute;left:80px;top:20px;width:100px;height:3px;background:var(--dark);border-radius:0 2px 2px 0}

/* back */
.hero-title{left:30px;top:16px;color:#fff}
.hero-title h1{font-family:"Playfair Display",Georgia,serif;font-weight:400;font-size:26px;line-height:1.15}
.hero-title p{font-family:"Playfair Display",Georgia,serif;font-size:12px;line-height:15.5px;margin-top:4px}
.spaces{left:29px;top:552px;width:412px;border:1px solid var(--line);border-radius:3px;overflow:hidden;border-collapse:collapse;font-size:7.4px;color:#333}
.spaces td{height:14.2px;padding:0;white-space:nowrap}
.spaces tr:nth-child(even) td{background:var(--row)}
.spaces td:first-child{padding-left:8px}
</style>
</head>
<body>

<section class="page page--front" aria-label="Flyer front">
  <svg class="art" width="461" height="652" viewBox="0 0 461 652">
    <defs>
      <linearGradient id="renderTone" x1="0" y1="0" x2="0" y2="1">
        <stop offset="0" stop-color="#6f9fd2"/>
        <stop offset=".3" stop-color="#d9e3ec"/>
        <stop offset=".55" stop-color="#b9b6ae"/>
        <stop offset=".78" stop-color="#55524d"/>
        <stop offset="1" stop-color="#2f2f31"/>
      </linearGradient>
    </defs>
    <polygon role="img" aria-label="Exterior rendering of the two-storey office building with parking lot" points="0,130 461,49 461,402 0,326" fill="url(#renderTone)"/>
    <polygon points="26,79 141,99 26,121" fill="var(--red)"/>
    <polygon points="26,332 241,372 241,652 26,652" fill="var(--red)"/>
  </svg>

  <div class="abs brand">The Marlowe</div>

  <div class="abs panel-text">
    <h2 class="panel-title">New<br>Riverside Office<br>/Medical Space</h2>
    <div class="rule" style="margin-top:10px"></div>
    <p class="address">New Riverside Village Bluffton,<br>South Carolina 29910</p>
    <div class="rule"></div>
    <h3 class="subhead">Property Highlights</h3>
    <ul class="highlights">
      <li><svg width="8" height="8" viewBox="0 0 8 8"><circle cx="4" cy="4" r="4" fill="#fff"/><path d="M2.2 4.1l1.2 1.2 2.4-2.5" stroke="var(--red)" stroke-width="1" fill="none"/></svg>Very high end class "A" Office / Medical space for lease in New Riverside Village.</li>
      <li><svg width="8" height="8" viewBox="0 0 8 8"><circle cx="4" cy="4" r="4" fill="#fff"/><path d="M2.2 4.1l1.2 1.2 2.4-2.5" stroke="var(--red)" stroke-width="1" fill="none"/></svg>Located at the Highway 170 &amp; Highway 46 Traffic Circle across from the New Riverside Harbor Market and close proximity to Marsh Point.</li>
      <li><svg width="8" height="8" viewBox="0 0 8 8"><circle cx="4" cy="4" r="4" fill="#fff"/><path d="M2.2 4.1l1.2 1.2 2.4-2.5" stroke="var(--red)" stroke-width="1" fill="none"/></svg>Great location and easy access from Highway 170 &amp; Highway 46 to Bluffton, Savannah, Hilton Head and Beaufort.</li>
      <li><svg width="8" height="8" viewBox="0 0 8 8"><circle cx="4" cy="4" r="4" fill="#fff"/><path d="M2.2 4.1l1.2 1.2 2.4-2.5" stroke="var(--red)" stroke-width="1" fill="none"/></svg>It's estimated that construction will begin early fall 2023 with an estimated delivery date in late 2024</li>
    </ul>
  </div>

  <h2 class="abs section-title" style="left:269px;top:411px">Offering Summary</h2>
  <div class="abs info-box" style="left:271px;top:433px;width:161px">
    <div class="info-row"><svg width="11" height="11" viewBox="0 0 11 11"><circle cx="5.5" cy="5.5" r="5.5" fill="var(--red)"/><path d="M3 5.6l1.7 1.7 3.3-3.4" stroke="#fff" stroke-width="1.3" fill="none"/></svg><b>1st Floor Available SF:</b><span>1,435, 1,722 &amp; 1,837 +/-RSF</span></div>
    <div class="info-row"><svg width="11" height="11" viewBox="0 0 11 11"><circle cx="5.5" cy="5.5" r="5.5" fill="var(--red)"/><path d="M3 5.6l1.7 1.7 3.3-3.4" stroke="#fff" stroke-width="1.3" fill="none"/></svg><b>2nd Floor Available SF:</b><span>1,435, 1,722 &amp; 1,837 +/- RSF</span></div>
    <div class="info-row"><svg width="11" height="11" viewBox="0 0 11 11"><circle cx="5.5" cy="5.5" r="5.5" fill="var(--red)"/><path d="M3 5.6l1.7 1.7 3.3-3.4" stroke="#fff" stroke-width="1.3" fill="none"/></svg><b>Base Rent for Year 1:</b><span>$43.00 PSF</span></div>
    <div class="info-row"><svg width="11" height="11" viewBox="0 0 11 11"><circle cx="5.5" cy="5.5" r="5.5" fill="var(--red)"/><path d="M3 5.6l1.7 1.7 3.3-3.4" stroke="#fff" stroke-width="1.3" fill="none"/></svg><b>Annual Increases:</b><span>3%</span></div>
    <div class="info-row"><svg width="11" height="11" viewBox="0 0 11 11"><circle cx="5.5" cy="5.5" r="5.5" fill="var(--red)"/><path d="M3 5.6l1.7 1.7 3.3-3.4" stroke="#fff" stroke-width="1.3" fill="none"/></svg><b>Type:</b><span>Office / Medical</span></div>
  </div>

  <h2 class="abs section-title" style="left:266px;top:592px;font-size:14px">For More Information</h2>
  <div class="abs contact">
    <div class="contact__name">Carter Haynes</div>
    <div class="contact__lines">
      <div><svg width="5" height="5" viewBox="0 0 10 10"><path d="M2 1l2 2-1 1.5c.8 1.4 1.6 2.2 3 3L7.5 6l2 2-1.5 1.5C4.5 9 1 5.5.5 2z" fill="var(--red)"/></svg> 555 210 4460 x2</div>
      <div><svg width="5" height="4" viewBox="0 0 10 8"><rect x=".5" y=".5" width="9" height="7" fill="none" stroke="var(--red)"/><path d="M.5.5l4.5 4 4.5-4" fill="none" stroke="var(--red)"/></svg> carter@lowcountryleasing.com</div>
    </div>
    <div class="contact__base"></div>
  </div>
</section>

<section class="page page--back" aria-label="Flyer back">
  <svg class="art" width="461" height="652" viewBox="0 0 461 652">
    <defs>
      <linearGradient id="marshTone" x1="0" y1="0" x2="0" y2="1">
        <stop offset="0" stop-color="#5f85b8"/>
        <stop offset=".35" stop-color="#b7b3c6"/>
        <stop offset=".55" stop-color="#ecb996"/>
        <stop offset=".68" stop-color="#d2cbc2"/>
        <stop offset=".8" stop-color="#6f9a3e"/>
        <stop offset="1" stop-color="#4f7d2c"/>
      </linearGradient>
      <linearGradient id="sunsetTone" x1="0" y1="0" x2="0" y2="1">
        <stop offset="0" stop-color="#8d7c98"/>
        <stop offset=".4" stop-color="#f1a65a"/>
        <stop offset=".6" stop-color="#b59a48"/>
        <stop offset=".8" stop-color="#e9a552"/>
        <stop offset="1" stop-color="#6b7634"/>
      </linearGradient>
    </defs>
    <polygon role="img" aria-label="Photo of salt marsh and river at dusk with a dock" points="0,0 461,0 461,391 0,310" fill="url(#marshTone)"/>
    <polygon points="0,0 282,0 241,82 0,124" fill="var(--red)"/>
    <polygon points="326,355 440,333 440,376" fill="#fff"/>
    <polygon role="img" aria-label="Photo of a marsh creek at sunset" points="218,378 438,417 438,533 218,533" fill="url(#sunsetTone)"/>
  </svg>

  <div class="abs hero-title">
    <h1>Available Spaces</h1>
    <p>Class "A" Office/Medical Space<br>New Riverside</p>
  </div>

  <h2 class="abs section-title" style="left:32px;top:369px">Lease Information</h2>
  <div class="abs info-box" style="left:33px;top:392px;width:161px">
    <div class="info-row"><svg width="11" height="11" viewBox="0 0 11 11"><circle cx="5.5" cy="5.5" r="5.5" fill="var(--red)"/><path d="M3 5.6l1.7 1.7 3.3-3.4" stroke="#fff" stroke-width="1.3" fill="none"/></svg><b>Lease Type:</b><span>NNN</span></div>
    <div class="info-row"><svg width="11" height="11" viewBox="0 0 11 11"><circle cx="5.5" cy="5.5" r="5.5" fill="var(--red)"/><path d="M3 5.6l1.7 1.7 3.3-3.4" stroke="#fff" stroke-width="1.3" fill="none"/></svg><b>Lease Term:</b><span>10 Years</span></div>
    <div class="info-row"><svg width="11" height="11" viewBox="0 0 11 11"><circle cx="5.5" cy="5.5" r="5.5" fill="var(--red)"/><path d="M3 5.6l1.7 1.7 3.3-3.4" stroke="#fff" stroke-width="1.3" fill="none"/></svg><b>Total Space:</b><span>1,435 - 4,994 RSF</span></div>
    <div class="info-row"><svg width="11" height="11" viewBox="0 0 11 11"><circle cx="5.5" cy="5.5" r="5.5" fill="var(--red)"/><path d="M3 5.6l1.7 1.7 3.3-3.4" stroke="#fff" stroke-width="1.3" fill="none"/></svg><b>Lease Rate:</b><span>$43.00 SF/yr</span></div>
  </div>

  <h2 class="abs section-title" style="left:33px;top:528px">Available Spaces</h2>
  <table class="abs spaces">
    <colgroup><col style="width:76px"><col style="width:84px"><col style="width:69px"><col style="width:60px"><col style="width:80px"><col></colgroup>
    <tr><td>100</td><td>Leased - Dentist</td><td>4,830 SF</td><td>NNN</td><td>$43.00 SF/yr</td><td>4,830 SF</td></tr>
    <tr><td>101</td><td>Available</td><td>1,837 SF</td><td>NNN</td><td>$43.00 SF/yr</td><td>1,600 SF</td></tr>
    <tr><td>102</td><td>Available</td><td>1,435 SF</td><td>NNN</td><td>$43.00 SF/yr</td><td>1,250 SF</td></tr>
    <tr><td>103</td><td>Available</td><td>1,722 SF</td><td>NNN</td><td>$43.00 SF/yr</td><td>1,500 SF</td></tr>
    <tr><td>101, 102 &amp; 103</td><td>Available</td><td>4,994 SF</td><td>NNN</td><td>$43.00 SF/yr</td><td>4,350 SF</td></tr>
  </table>
</section>

</body>
</html>
```